Black Friday Sale - Banner

Black Friday Sale. for website
https://velmorabeautyworks.com/
Our Black Friday sale includes a free product with a purchase of any flat iron.
banner size is 1880x720
Must include Black Friday Deal
Free Heat Protectant Spray with all purchases
Target Market(s)
Hair Care Professionals
Industry/Entity Type
Beauty Salon
Font styles to use
Sans Serif
Colors
86cae7
ec1f27
ffffff
Requirements
Must have
- Must have a photo image of the product that is free
Can include images of flat irons from website
Nice to have
- images from website
Should not have
- white person

```html
<!DOCTYPE html>
<html lang="en">
<head>
<meta charset="utf-8">
<title>Black Friday Deal – Velmora Beauty Works</title>
<link rel="stylesheet" href="https://fonts.googleapis.com/css2?family=Kaushan+Script&family=Roboto+Slab:wght@800&family=Oswald:wght@500;600&display=swap">
<style>
  :root {
    --page: #f4f4f4;
    --navy-deep: #0c0c24;
    --navy: #1b1d48;
    --glow-blue: #2c5fd4;
    --sky: #86cae7;
    --deal-blue: #b9dcff;
    --red: #ec1f27;
    --ribbon-red: #cf1231;
    --white: #ffffff;
  }
  html, body {
    margin: 0;
    width: 1200px;
    height: 1200px;
    overflow: hidden;
    background: var(--page);
  }
  .sale-banner {
    position: absolute;
    left: 40px;
    top: 329px;
    width: 1120px;
    height: 542px;
    display: block;
  }
  .headline-script {
    font-family: "Kaushan Script", cursive;
    font-size: 175px;
    fill: var(--red);
  }
  .headline-slab {
    font-family: "Roboto Slab", serif;
    font-weight: 800;
    font-size: 168px;
    fill: var(--deal-blue);
  }
  .offer-big {
    font-family: "Oswald", sans-serif;
    font-weight: 600;
    font-size: 168px;
    fill: var(--white);
  }
  .offer-small {
    font-family: "Oswald", sans-serif;
    font-weight: 500;
    font-size: 56px;
    fill: var(--white);
  }
</style>
</head>
<body>
<svg class="sale-banner" viewBox="0 0 1725 835" xmlns="http://www.w3.org/2000/svg" aria-label="Black Friday Deal banner for Velmora Beauty Works">
  <defs>
    <linearGradient id="wall" x1="0" y1="0" x2="1" y2="1">
      <stop offset="0" stop-color="var(--navy)"/>
      <stop offset="1" stop-color="var(--navy-deep)"/>
    </linearGradient>
    <radialGradient id="blue-glow" cx="0.5" cy="0.5" r="0.5">
      <stop offset="0" stop-color="var(--glow-blue)" stop-opacity="0.75"/>
      <stop offset="1" stop-color="var(--glow-blue)" stop-opacity="0"/>
    </radialGradient>
    <radialGradient id="red-glow" cx="0.5" cy="0.5" r="0.5">
      <stop offset="0" stop-color="var(--red)" stop-opacity="0.45"/>
      <stop offset="1" stop-color="var(--red)" stop-opacity="0"/>
    </radialGradient>
    <linearGradient id="bottle" x1="0" y1="0" x2="0" y2="1">
      <stop offset="0" stop-color="#ffffff"/>
      <stop offset="0.72" stop-color="#f1f1f1"/>
      <stop offset="0.74" stop-color="#f2711c"/>
      <stop offset="1" stop-color="#e8661a"/>
    </linearGradient>
    <filter id="soft-glow" x="-20%" y="-20%" width="140%" height="140%">
      <feGaussianBlur stdDeviation="6" result="b"/>
      <feMerge><feMergeNode in="b"/><feMergeNode in="SourceGraphic"/></feMerge>
    </filter>
  </defs>

  <!-- wall -->
  <rect class="wall" width="1725" height="835" fill="url(#wall)" role="img" aria-label="Dark navy brick wall background"/>
  <ellipse cx="470" cy="400" rx="430" ry="230" fill="url(#blue-glow)"/>
  <ellipse cx="440" cy="180" rx="260" ry="130" fill="url(#red-glow)"/>

  <!-- headline frame -->
  <g class="headline-frame" fill="none" stroke="var(--red)" stroke-width="5">
    <polyline points="188,207 70,220 90,643 305,630"/>
    <polyline points="700,161 913,149 932,545 715,575"/>
  </g>

  <!-- accent slashes -->
  <g class="accent-lines" fill="var(--red)">
    <polygon points="680,108 925,83 680,117"/>
    <polygon points="320,745 970,630 320,758"/>
    <polygon points="135,677 305,660 135,680"/>
    <polygon points="720,607 885,588 720,611"/>
  </g>

  <!-- pedestal -->
  <polygon class="pedestal" points="340,565 685,525 715,625 305,675" fill="var(--red)"/>
  <polygon points="340,565 355,640 305,675" fill="#8a0c1a"/>
  <polygon points="685,525 680,605 715,625" fill="#8a0c1a"/>

  <!-- headline -->
  <text class="headline-script" x="215" y="270" textLength="450" lengthAdjust="spacingAndGlyphs" transform="rotate(-8 440 200)" filter="url(#soft-glow)">Black</text>
  <text class="headline-slab" x="112" y="535" textLength="770" lengthAdjust="spacingAndGlyphs" transform="rotate(-7 500 470)" filter="url(#soft-glow)">Friday Deal</text>

  <!-- offer ribbon -->
  <polygon class="offer-ribbon" points="1025,110 1360,57 1363,80 1325,85 1325,695 1185,650 1053,805 1053,125" fill="var(--ribbon-red)"/>
  <text class="offer-big" x="1192" y="290" text-anchor="middle" textLength="205" lengthAdjust="spacingAndGlyphs">FREE</text>
  <g class="offer-lines" text-anchor="middle">
    <text class="offer-small" x="1190" y="385" textLength="70" lengthAdjust="spacingAndGlyphs">HEAT</text>
    <text class="offer-small" x="1190" y="455" textLength="172" lengthAdjust="spacingAndGlyphs">PROTECTANT</text>
    <text class="offer-small" x="1186" y="527" textLength="164" lengthAdjust="spacingAndGlyphs">SPRAY WITH</text>
    <text class="offer-small" x="1188" y="597" textLength="215" lengthAdjust="spacingAndGlyphs">ALL PURCHASES</text>
  </g>

  <!-- product -->
  <rect class="product-photo" x="1362" y="63" width="135" height="662" rx="40" fill="url(#bottle)" role="img" aria-label="Photo of the free heat protectant spray bottle, white with orange base"/>
</svg>
</body>
</html>
```